Display Carton for cinnamon sticks

Display Box Specification – Valle del Sol Dorado Cinnamon Sticks
Design a retail-ready display box for Valle del Sol Dorado cinnamon sticks, sourced from Sri Lanka. Each selling unit contains two 5" cinnamon sticks, individually sealed in a clear cellophane wrapper to preserve freshness and showcase product quality.
📦 Carton Configuration
• Total Units per Display: 32 wrappers
• Layering Structure: 8 wrappers per layer × 4 layers high
• Orientation: Wrappers laid flat, stacked horizontally for optimal visibility and ease of access
I uploaded 2 AI-generated images for reference purposes only

Target Market(s)

Cultural Appeal Suggestions Color Palette: Use warm, earthy tones like terracotta, deep reds, and golds—colors often associated with Latin American aesthetics. Typography: Consider a bold, rustic font with a handcrafted feel to evoke authenticity. Language: Include bilingual labeling (English & Spanish). For example: “Cinnamon Sticks” → “Palitos de Canela” “Sourced from Sri Lanka” → “Origen: Sri Lanka” Storytelling Element: Add a short cultural or culinary note about how cinnamon is used in Latin cuisine (e.g., in café de olla, arroz con leche, or ponche).

Font styles to use
Other font styles liked:
• Consider a bold, rustic font with a handcrafted feel to evoke authenticity.

Requirements
Nice to have
• 📦 Display Box Messaging Front panel: “Valle del Sol Dorado – Premium Canela de Ceilán” (Ceylon Cinnamon – Naturally Sweet & Aromatic) Side panel: “Perfect for traditional recipes and everyday flavor” (Ideal para recetas tradicionales y sabor diario)

```html
<!DOCTYPE html>
<html lang="en">
<head>
<meta charset="utf-8">
<title>Valle del Sol Dorado – Cinnamon Sticks Carton</title>
<link rel="stylesheet" href="https://fonts.googleapis.com/css2?family=Cinzel:wght@600;700&family=Roboto:wght@400&display=swap">
<style>
  :root {
    --backdrop: #d7d7d7;
    --bark: #6a2e20;
    --gold: #e8b82c;
    --gold-line: #d9a41f;
    --cream: #f4ead6;
    --ink: #2a1a15;
    --band-ink: #8a5a12;
    --top-light: #f8c772;
    --top-deep: #f0b04e;
    --side-orange: #e69a2c;
    --fold: rgba(120, 70, 10, 0.35);
    --stick-light: #d08a55;
    --stick-dark: #8e4a26;
  }
  html, body {
    margin: 0;
    width: 1200px;
    height: 800px;
    overflow: hidden;
    background: var(--backdrop);
  }
  .carton-net { display: block; width: 1200px; height: 800px; }
  .display { font-family: "Cinzel", serif; font-weight: 700; fill: var(--ink); }
  .band-text { font-family: "Cinzel", serif; font-weight: 700; fill: var(--band-ink); }
  .body-copy { font-family: "Roboto", sans-serif; font-weight: 400; fill: var(--ink); }
</style>
</head>
<body>
<svg class="carton-net" viewBox="0 0 1200 800" xmlns="http://www.w3.org/2000/svg" aria-label="Cinnamon sticks carton, flat panels">
  <defs>
    <linearGradient id="top-tone" x1="0" y1="0" x2="1" y2="1">
      <stop offset="0" stop-color="var(--top-light)"/>
      <stop offset="1" stop-color="var(--top-deep)"/>
    </linearGradient>
    <linearGradient id="stick-tone" x1="0" y1="0" x2="1" y2="1">
      <stop offset="0" stop-color="var(--stick-light)"/>
      <stop offset="1" stop-color="var(--stick-dark)"/>
    </linearGradient>
    <clipPath id="label-shape">
      <path d="M215,0 L745,0 C720,70 760,150 840,125 C860,250 820,420 870,540 L95,540 C120,420 80,250 130,150 C200,140 240,70 215,0 Z"/>
    </clipPath>
    <path id="title-arc" d="M220,512 Q480,440 750,348"/>
  </defs>

  <!-- Top panel (printed to read from the back of the carton) -->
  <g class="top-panel" transform="translate(430,60) rotate(180 320 150)">
    <rect width="640" height="300" fill="url(#top-tone)" stroke="var(--fold)" stroke-width="1"/>

    <g class="top-brand">
      <circle cx="66" cy="82" r="26" fill="var(--ink)"/>
      <text class="display" x="102" y="76" font-size="22">VALLE DEL</text>
      <text class="display" x="102" y="102" font-size="22">SOL DORADO™</text>
    </g>
    <text class="display" x="40" y="162" font-size="18" letter-spacing="1">CINNAMON STICKS</text>
    <g class="top-count">
      <text class="display" x="40" y="252" font-size="64">25</text>
      <text class="display" x="136" y="250" font-size="18" letter-spacing="1">STICKS</text>
    </g>

    <g class="top-message">
      <text class="display" x="290" y="62" font-size="12" letter-spacing="0.5">PERFECT FOR TRADITIONAL RECIPES</text>
      <text class="display" x="290" y="80" font-size="12" letter-spacing="0.5">AND EVERYDAY FLAVOR</text>
      <text class="display" x="290" y="98" font-size="12" letter-spacing="0.5">(IDEAL PARA RECETAS TRADICIONALES Y</text>
      <text class="display" x="290" y="116" font-size="12" letter-spacing="0.5">SABOR DIARIO)</text>
      <line x1="290" y1="132" x2="612" y2="132" stroke="var(--ink)" stroke-width="1.2"/>
      <text class="body-copy" x="290" y="154" font-size="11">Lorem ipsum dolor sit amet, consectetur adipiscing elit.</text>
      <text class="body-copy" x="290" y="170" font-size="11">Nulla ac sapien non tellus blandit fringilla.</text>
      <text class="body-copy" x="290" y="190" font-size="11">Pellentesque at elit molestie, gravida</text>
      <text class="body-copy" x="290" y="205" font-size="11">dui non, venenatis erat.</text>
      <text class="body-copy" x="290" y="220" font-size="11">Proin eget risus eu purus mollis porta.</text>
    </g>

    <g class="top-origin">
      <rect x="290" y="238" width="52" height="44" rx="4" fill="#c98f35" role="img" aria-label="Heraldic emblem illustration of Ceylon origin"/>
      <text class="display" x="354" y="252" font-size="11" letter-spacing="3">PREMIUM</text>
      <text class="display" x="354" y="266" font-size="11" letter-spacing="2">CANELA DE</text>
      <text class="display" x="354" y="288" font-size="22" letter-spacing="1">CEILÁN</text>
    </g>
  </g>

  <!-- Side panel (text runs along the panel height) -->
  <g class="side-panel" transform="translate(430,360) rotate(90)">
    <rect width="360" height="300" fill="var(--side-orange)" stroke="var(--fold)" stroke-width="1"/>

    <g class="side-brand">
      <circle cx="34" cy="40" r="16" fill="var(--ink)"/>
      <text class="display" x="56" y="36" font-size="12">VALLE DEL</text>
      <text class="display" x="56" y="52" font-size="12">SOL DORADO™</text>
    </g>
    <text class="display" x="20" y="130" font-size="11" letter-spacing="0.5">CINAMON STICKS</text>
    <g class="side-count">
      <text class="display" x="20" y="270" font-size="56">25</text>
      <text class="display" x="98" y="268" font-size="11" letter-spacing="1">STICKS</text>
    </g>

    <g class="side-message">
      <text class="display" x="172" y="30" font-size="7.5">PERFECT FOR TRADITIONAL RECIPES</text>
      <text class="display" x="172" y="42" font-size="7.5">AND EVERYDAY FLAVOR</text>
      <text class="display" x="172" y="54" font-size="7.5">(IDEAL PARA RECETAS</text>
      <text class="display" x="172" y="66" font-size="7.5">TRADICIONALES Y SABOR DIARIO)</text>
      <line x1="172" y1="78" x2="345" y2="78" stroke="var(--ink)" stroke-width="1"/>
      <text class="body-copy" x="172" y="94" font-size="8">Lorem ipsum dolor sit amet, consectetur</text>
      <text class="body-copy" x="172" y="105" font-size="8">adipiscing elit. Nulla ac sapien non</text>
      <text class="body-copy" x="172" y="116" font-size="8">tellus blandit fringilla.</text>
      <text class="body-copy" x="172" y="132" font-size="8">Pellentesque at elit molestie, gravida</text>
      <text class="body-copy" x="172" y="143" font-size="8">dui non, venenatis erat.</text>
      <text class="body-copy" x="172" y="154" font-size="8">Proin eget risus eu purus mollis porta.</text>
    </g>

    <g class="side-origin">
      <rect x="172" y="228" width="40" height="36" rx="3" fill="#c07f22" role="img" aria-label="Heraldic emblem illustration of Ceylon origin"/>
      <text class="display" x="220" y="240" font-size="9" letter-spacing="2">PREMIUM</text>
      <text class="display" x="220" y="252" font-size="9" letter-spacing="1">CANELA DE</text>
      <text class="display" x="220" y="270" font-size="17">CEILÁN</text>
    </g>
  </g>

  <!-- Front panel -->
  <svg class="front-panel" x="430" y="360" width="640" height="360" viewBox="0 0 960 540">
    <rect class="panel-ground" width="960" height="540" fill="var(--bark)"/>
    <g class="label" clip-path="url(#label-shape)">
      <rect width="960" height="540" fill="var(--cream)"/>
      <rect class="top-band" width="960" height="112" fill="var(--gold)"/>
    </g>
    <path class="label-edge" d="M215,0 L745,0 C720,70 760,150 840,125 C860,250 820,420 870,540 L95,540 C120,420 80,250 130,150 C200,140 240,70 215,0 Z" fill="none" stroke="var(--gold-line)" stroke-width="10"/>

    <g class="origin-band">
      <circle cx="395" cy="58" r="16" fill="none" stroke="var(--band-ink)" stroke-width="2"/>
      <text class="band-text" x="425" y="50" font-size="14" letter-spacing="1.5">PREMIUM CANELA</text>
      <text class="band-text" x="425" y="76" font-size="24" letter-spacing="1">DE CEILÁN</text>
    </g>

    <g class="brand-lockup">
      <circle cx="360" cy="178" r="32" fill="var(--ink)"/>
      <text class="display" x="408" y="168" font-size="32" letter-spacing="1">VALLE DEL</text>
      <text class="display" x="408" y="204" font-size="32" letter-spacing="1">SOL DORADO™</text>
    </g>

    <rect class="product-photo" x="420" y="240" width="110" height="115" rx="6" fill="url(#stick-tone)" role="img" aria-label="Photo of a bundle of cinnamon sticks"/>

    <text class="display" font-size="42" letter-spacing="3">
      <textPath href="#title-arc" startOffset="50%" text-anchor="middle">CINAMON STICKS</textPath>
    </text>
  </svg>
</svg>
</body>
</html>
```